Voranta Imports Busisness cards and logo

Voranta imports is a brand new wholesale company located in Londonderry, New Hampshire dedicated to finding unique products from around the world.
Licensed to sell wine and spirits in the state and also authorized distributors of Pale Meadow Design, a manufacturer of girls and women shoes. Other products that we are currently trying to import are cheese and frozen food from Spain.
We would like a design that portraits our diversity of products and wholesale capabilities

```html
<!DOCTYPE html>
<html lang="en">
<head>
<meta charset="utf-8">
<title>Voranta Imports — Business Card</title>
<link rel="stylesheet" href="https://fonts.googleapis.com/css2?family=Open+Sans:wght@400;600;700&display=swap">
<style>
  :root {
    --page-bg: #d9d5cf;
    --card-white: #ffffff;
    --card-shade: #e6e6e6;
    --ink: #333333;
    --ink-soft: #444444;
    --brand-green: #3f7f27;
    --green-light: #7dbb42;
    --green-dark: #3d7a2c;
    --band-grey: #8d8d8d;
    --band-grey-light: #c4c4c4;
    --icon-bg: #3a3a3a;
  }
  * { margin: 0; padding: 0; box-sizing: border-box; }
  html, body { width: 1200px; height: 899px; overflow: hidden; }
  body {
    background: var(--page-bg);
    font-family: "Open Sans", Arial, sans-serif;
    position: relative;
  }
  .card {
    position: absolute;
    left: 100px; top: 164px;
    width: 1000px; height: 571px;
    background: radial-gradient(ellipse at 48% 62%, var(--card-white) 0%, var(--card-white) 30%, var(--card-shade) 100%);
    box-shadow: 0 12px 30px rgba(0,0,0,0.22);
    overflow: hidden;
  }
  .card__swoosh { position: absolute; inset: 0; width: 100%; height: 100%; }
  .brand {
    position: absolute;
    left: 48px; top: 52px;
    display: flex; align-items: center; gap: 22px;
  }
  .brand__dot {
    width: 96px; height: 96px; border-radius: 50%;
    background: var(--brand-green);
  }
  .brand__name {
    font-weight: 700;
    font-size: 58px;
    letter-spacing: -1px;
    color: var(--brand-green);
  }
  .contact {
    position: absolute;
    left: 48px; top: 224px;
    list-style: none;
    font-size: 21px;
    color: var(--ink);
    line-height: 1.2;
  }
  .contact__item {
    display: flex; align-items: flex-start; gap: 10px;
    margin-bottom: 7px;
  }
  .contact__icon {
    flex: 0 0 22px; width: 22px; height: 22px; margin-top: 2px;
  }
  .holder {
    position: absolute;
    right: 150px; bottom: 56px;
    text-align: right;
  }
  .holder__name {
    font-weight: 700; font-size: 40px; color: var(--ink);
  }
  .holder__role {
    font-weight: 400; font-size: 36px; color: var(--ink-soft);
  }
</style>
</head>
<body>
  <div class="card">
    <svg class="card__swoosh" viewBox="0 0 1000 571" preserveAspectRatio="none" aria-hidden="true">
      <defs>
        <linearGradient id="band-grey" x1="0" y1="0" x2="1" y2="1">
          <stop offset="0" stop-color="var(--band-grey-light)"/>
          <stop offset="0.5" stop-color="var(--band-grey)"/>
          <stop offset="1" stop-color="var(--band-grey-light)"/>
        </linearGradient>
        <linearGradient id="band-green" x1="0" y1="0" x2="1" y2="1">
          <stop offset="0" stop-color="var(--green-dark)"/>
          <stop offset="1" stop-color="var(--green-light)"/>
        </linearGradient>
      </defs>
      <path d="M560,0 C770,70 930,270 960,571 L1000,571 L1000,0 Z" fill="url(#band-grey)"/>
      <path d="M640,0 C820,70 960,250 1000,470 L1000,0 Z" fill="url(#band-green)"/>
      <path d="M790,150 C890,235 965,360 1000,470 L1000,510 C955,380 885,255 790,150 Z" fill="url(#band-grey)"/>
    </svg>

    <div class="brand">
      <span class="brand__dot"></span>
      <span class="brand__name">Voranta Imports</span>
    </div>

    <ul class="contact">
      <li class="contact__item">
        <svg class="contact__icon" viewBox="0 0 22 22"><circle cx="11" cy="11" r="11" fill="var(--icon-bg)"/><path d="M5 11.5 11 6l6 5.5h-2V16h-2.6v-3h-2.8v3H7v-4.5Z" fill="#fff"/></svg>
        <span>Suite # 214, Mammoth Rd,<br>Londonderry, NH 03053</span>
      </li>
      <li class="contact__item">
        <svg class="contact__icon" viewBox="0 0 22 22"><circle cx="11" cy="11" r="11" fill="var(--icon-bg)"/><path d="M7 6c1-.8 2-.5 2.4.4l.8 1.8c.2.5 0 1-.4 1.3l-.7.5c.6 1.4 1.6 2.4 3 3l.5-.7c.3-.4.9-.6 1.3-.4l1.8.8c.9.4 1.2 1.4.4 2.4-2.6 2.2-10.3-5.5-8.1-8.1Z" fill="#fff"/></svg>
        <span>603-555-0142</span>
      </li>
      <li class="contact__item">
        <svg class="contact__icon" viewBox="0 0 22 22"><circle cx="11" cy="11" r="11" fill="var(--icon-bg)"/><rect x="7.5" y="4.5" width="7" height="13" rx="1.2" fill="#fff"/><rect x="8.7" y="6" width="4.6" height="8" fill="var(--icon-bg)"/></svg>
        <span>603-555-0187</span>
      </li>
      <li class="contact__item">
        <svg class="contact__icon" viewBox="0 0 22 22"><circle cx="11" cy="11" r="11" fill="var(--icon-bg)"/><rect x="5" y="9" width="12" height="7" rx="1" fill="#fff"/><rect x="7.5" y="5" width="7" height="4" fill="#fff"/></svg>
        <span>603-555-0163</span>
      </li>
      <li class="contact__item">
        <svg class="contact__icon" viewBox="0 0 22 22"><circle cx="11" cy="11" r="11" fill="var(--icon-bg)"/><rect x="5" y="7" width="12" height="8.5" rx="1" fill="#fff"/><path d="M5.5 7.5 11 12l5.5-4.5" stroke="var(--icon-bg)" stroke-width="1.3" fill="none"/></svg>
        <span>daniel@vorantaimports.com</span>
      </li>
      <li class="contact__item">
        <svg class="contact__icon" viewBox="0 0 22 22"><circle cx="11" cy="11" r="11" fill="var(--icon-bg)"/><g stroke="#fff" stroke-width="1.3" fill="none"><circle cx="11" cy="11" r="6"/><ellipse cx="11" cy="11" rx="2.6" ry="6"/><path d="M5 11h12"/></g></svg>
        <span>www.vorantaimports.com</span>
      </li>
    </ul>

    <div class="holder">
      <p class="holder__name">Daniel Crane</p>
      <p class="holder__role">Owner / C.E.O</p>
    </div>
  </div>
</body>
</html>
```